Business Card Design

We are a manufacturing and distribution company with most of our customer base being supermarkets. We have established brand guidelines that are attached.

```html
<!DOCTYPE html>
<html lang="en">
<head>
<meta charset="utf-8">
<title>Corvelle — Business Card</title>
<link rel="stylesheet" href="https://fonts.googleapis.com/css2?family=Montserrat:wght@700;800&family=Arimo:wght@400&display=swap">
<style>
  :root {
    --stage: #3a3d44;
    --card-dark: #1e1e1e;
    --card-light: #ffffff;
    --brand-blue: #0068ad;
    --brand-red: #e31b23;
    --ink: #1a1a1a;
    --paper-text: #ffffff;
  }
  * { box-sizing: border-box; margin: 0; padding: 0; }
  html, body { width: 1200px; height: 1000px; overflow: hidden; }
  body {
    background: var(--stage);
    font-family: "Arimo", Arial, sans-serif;
    position: relative;
  }
  .card {
    position: absolute;
    left: 220px;
    width: 760px;
    height: 434px;
    border-radius: 22px;
    overflow: hidden;
    box-shadow: 0 14px 30px rgba(0,0,0,0.45);
  }
  .card--back { top: 50px; background: var(--card-dark); }
  .card--front { top: 516px; background: var(--card-light); }

  .accent-band {
    position: absolute;
    top: 0;
    height: 100%;
  }
  .card--back .accent-band {
    left: 0;
    width: 250px;
    background: var(--brand-blue);
  }
  .card--front .accent-band {
    right: 0;
    width: 270px;
    background: var(--brand-red);
  }

  .brand-lockup {
    position: absolute;
    right: 56px;
    bottom: 60px;
    display: flex;
    align-items: center;
    gap: 16px;
  }
  .brand-lockup__square {
    width: 34px;
    height: 34px;
    background: var(--brand-blue);
  }
  .brand-name {
    font-family: "Montserrat", Arial, sans-serif;
    font-weight: 800;
    letter-spacing: 0.04em;
    text-transform: uppercase;
    line-height: 1;
  }
  .card--back .brand-name { color: var(--paper-text); font-size: 64px; }

  .front-content {
    position: absolute;
    left: 48px;
    top: 42px;
    width: 420px;
    color: var(--ink);
  }
  .card--front .brand-name { color: var(--ink); font-size: 58px; }

  .person {
    margin-top: 26px;
    font-family: "Montserrat", Arial, sans-serif;
    font-weight: 800;
    font-size: 27px;
    letter-spacing: 0.06em;
    text-transform: uppercase;
    line-height: 1;
  }
  .person__first { color: var(--brand-red); }
  .person__last { color: var(--brand-blue); }
  .role { font-size: 17px; margin-top: 6px; }

  .address { margin-top: 26px; font-size: 17px; line-height: 1.35; font-style: normal; }

  .contact-list { list-style: none; margin-top: 20px; font-size: 17px; }
  .contact-list li { display: flex; align-items: center; gap: 10px; line-height: 1.5; }
  .contact-list svg { width: 16px; height: 16px; fill: var(--brand-blue); flex: none; }
</style>
</head>
<body>

<section class="card card--back" aria-label="Card back">
  <div class="accent-band"></div>
  <div class="brand-lockup">
    <span class="brand-lockup__square"></span>
    <span class="brand-name">Corvelle</span>
  </div>
</section>

<section class="card card--front" aria-label="Card front">
  <div class="accent-band"></div>
  <div class="front-content">
    <h1 class="brand-name">Corvelle</h1>
    <p class="person"><span class="person__first">Dana</span> <span class="person__last">Whitlow</span></p>
    <p class="role">CEO/Founder</p>
    <address class="address">4120 Harlow Street<br>Sample City, ST 20415</address>
    <ul class="contact-list">
      <li>
        <svg viewBox="0 0 24 24" aria-hidden="true"><path d="M6.6 10.8a15 15 0 0 0 6.6 6.6l2.2-2.2a1 1 0 0 1 1-.25 11.4 11.4 0 0 0 3.6.57 1 1 0 0 1 1 1V20a1 1 0 0 1-1 1A17 17 0 0 1 3 4a1 1 0 0 1 1-1h3.5a1 1 0 0 1 1 1c0 1.25.2 2.45.57 3.57a1 1 0 0 1-.25 1z"/></svg>
        555-014-2290
      </li>
      <li>
        <svg viewBox="0 0 24 24" aria-hidden="true"><path d="M2 5h20v14H2zm2 2v.5l8 5 8-5V7l-8 5z"/></svg>
        info@corvelle.example
      </li>
      <li>
        <svg viewBox="0 0 24 24" aria-hidden="true"><circle cx="12" cy="12" r="10"/></svg>
        www.corvelle.example
      </li>
    </ul>
  </div>
</section>

</body>
</html>
```